Business card for denture clinic Veltrimora

We need a new business card with our new logo. We are a denture clinic in New Zealand with our target market being 45+ years old. We would need a space on the back to write our patients next appointment on. We would space for only one appointment rather than a list. We will attach a photo showing an example of this. But of course, we would like to see your twist on this. We want it to be bold and easy to read and a good mixture of professional but modern. We have attached our logo to be used on the card.

Target Market(s)

People aged 45+ needing dentures

Industry/Entity Type

Dental

Contact Information for Business Card

We want our logo on the front and the space to write an appointment on the back. I've attached an example our our old business card showing this. We need to have the technicians details on the front.

Font styles to use
Sans Serif

Colors
0255a3
919191
fbfbfb

Requirements
Must have
• The following details:
• Liam Dorsett BDT, PGDipCDentTech Calverin
• Dental Prosthetist
• Phone numbers: 0800 47 3125
• 09 572 1394
• Email: liam@veltrimora.co.nz
• www.veltrimora.co.nz
• Address: 14 Marlow Crest Road
• Halbrook West
• Auckland 0793
Nice to have
• We would like our business cards to have more than just two colours as we want them to be more vibrant. We have uploaded an example of a business card we liked that showed this.

```html
<!DOCTYPE html>
<html lang="en">
<head>
<meta charset="utf-8">
<title>Veltrimora Business Card</title>
<link href="https://fonts.googleapis.com/css2?family=Exo+2:ital,wght@0,400;0,500;0,600;0,700;1,400&display=swap" rel="stylesheet">
<style>
  :root {
    --brand-blue: #0168b5;
    --deep-blue: #0255a3;
    --grey: #919191;
    --dark-grey: #555555;
    --rule-grey: #7a7a7a;
    --card-white: #fbfbfb;
    --tagline-light: #cfe3f5;
    --backdrop: #e8e5e0;
  }
  * { margin: 0; padding: 0; box-sizing: border-box; }
  html, body {
    width: 1200px; height: 987px; overflow: hidden;
    background: var(--backdrop);
    font-family: "Exo 2", sans-serif;
  }
  .canvas { position: relative; width: 1200px; height: 987px; }
  .card {
    position: absolute; left: 293px; width: 615px; height: 351px;
    border-radius: 16px; overflow: hidden; background: var(--card-white);
    box-shadow: 0 3px 8px rgba(0,0,0,0.25);
  }
  .card-front { top: 129px; }
  .card-back { top: 506px; height: 349px; }

  /* front */
  .front-brand { position: absolute; left: 329px; top: 44px; width: 285px; text-align: center; }
  .brand-square {
    display: block; margin: 0 auto 8px; width: 55px; height: 55px;
    background: var(--brand-blue);
  }
  .brand-name {
    font-weight: 600; color: var(--brand-blue); font-size: 27px;
    letter-spacing: 1px; line-height: 1;
  }
  .brand-tagline {
    font-size: 11px; letter-spacing: 2.6px; color: var(--grey); margin-top: 5px;
  }
  .person { position: absolute; left: 29px; top: 172px; }
  .person-name { font-size: 22px; font-weight: 700; color: var(--brand-blue); }
  .person-name .credentials { font-size: 16px; font-weight: 600; }
  .person-role { font-size: 16px; color: var(--dark-grey); margin-top: 2px; }
  .divider {
    position: absolute; left: 29px; top: 238px; width: 562px; height: 1px;
    background: var(--rule-grey);
  }
  .contact { position: absolute; left: 29px; top: 246px; font-size: 16px; color: var(--dark-grey); line-height: 24px; }
  .contact .label { color: var(--brand-blue); font-weight: 700; }
  .contact .email { font-size: 15px; }
  .address {
    position: absolute; right: 24px; top: 246px; text-align: right;
    font-size: 16px; color: var(--dark-grey); line-height: 21px;
  }
  .front-footer { position: absolute; left: 0; bottom: 0; width: 615px; height: 36px; }
  .website {
    position: absolute; right: 24px; bottom: 9px; color: #ffffff;
    font-size: 16px; font-style: italic; letter-spacing: 0.5px;
  }

  /* back */
  .back-header {
    position: absolute; left: 0; top: 0; width: 100%; height: 193px;
    background: var(--brand-blue); text-align: center; padding-top: 48px;
  }
  .back-header .brand-square { width: 63px; height: 63px; background: #ffffff; margin-bottom: 10px; }
  .back-header .brand-name { color: #ffffff; font-size: 31px; }
  .back-header .brand-tagline { color: var(--tagline-light); font-size: 13px; letter-spacing: 3px; margin-top: 6px; }
  .appointment {
    position: absolute; left: 40px; top: 193px; width: 535px; height: 135px;
    display: flex; align-items: center;
  }
  .appointment-row {
    display: flex; font-size: 19px; font-style: italic; color: var(--dark-grey);
    align-items: flex-end; width: 100%;
  }
  .appointment-row .field { display: flex; align-items: flex-end; }
  .appointment-row .dots {
    display: inline-block; border-bottom: 2px dotted var(--grey); height: 14px; margin: 0 3px 4px;
  }
  .appointment-row .date .dots { width: 200px; }
  .appointment-row .time { margin-left: 14px; }
  .appointment-row .time .dots { width: 150px; }
  .back-footer { position: absolute; left: 0; bottom: 0; width: 100%; height: 21px; background: var(--brand-blue); }
</style>
</head>
<body>
<div class="canvas">

  <section class="card card-front">
    <div class="front-brand">
      <span class="brand-square"></span>
      <div class="brand-name">VELTRIMORA</div>
      <div class="brand-tagline">THE DENTURE EXPERTS</div>
    </div>

    <div class="person">
      <div class="person-name">LIAM DORSETT <span class="credentials">BDT, PGDipCDentTech Calverin</span></div>
      <div class="person-role">Dental Prosthetist</div>
    </div>

    <div class="divider"></div>

    <div class="contact">
      <div><span class="label">P</span> : 0800 47 3125</div>
      <div><span class="label">C</span> : 09 572 1394</div>
      <div class="email">liam@veltrimora.co.nz</div>
    </div>

    <div class="address">
      <div>14 Marlow Crest Road</div>
      <div>Halbrook West</div>
      <div>Auckland 0793</div>
    </div>

    <svg class="front-footer" viewBox="0 0 615 36" preserveAspectRatio="none" aria-hidden="true">
      <polygon points="0,20 350,20 342,31 0,31" fill="#7d7d7d"/>
      <polygon points="0,31 615,31 615,36 0,36" fill="#0168b5"/>
      <polygon points="370,0 615,0 615,36 335,36" fill="#0168b5"/>
    </svg>
    <div class="website">www.veltrimora.co.nz</div>
  </section>

  <section class="card card-back">
    <header class="back-header">
      <span class="brand-square"></span>
      <div class="brand-name">VELTRIMORA</div>
      <div class="brand-tagline">THE DENTURE EXPERTS</div>
    </header>

    <div class="appointment">
      <div class="appointment-row">
        <span class="field date">date:<span class="dots"></span></span>
        <span class="field time">time:<span class="dots"></span>am/pm</span>
      </div>
    </div>

    <div class="back-footer"></div>
  </section>

</div>
</body>
</html>
```